Option Sheet

We need a one page option sheet with a left to right reading of the five options. It should be a one sheet, multiple colors and definitive separations between options This is used in a sales consultation. Backround or colors not in option need to have the follow RGB value (5 red, 20 green, 63 blue)

We added a smaller text file, please change that point

Target Market(s)

Divorce

Industry/Entity Type

Legal

Requirements
Must have
• 1) All five options left to right
• 2)language included in sheet

```html
<!DOCTYPE html>
<html lang="en">
<head>
<meta charset="utf-8">
<title>Five Options – Divorce</title>
<link rel="stylesheet" href="https://fonts.googleapis.com/css2?family=Bebas+Neue&family=Oswald:wght@400;500&family=Open+Sans:wght@400;600&display=swap">
<style>
  :root {
    --ink: #4b4b4d;
    --text: #3a3a3a;
    --rule: #dcdcdc;
    --paper: #ffffff;
    --frame: #e4e4e4;
    --blue: #4a73b7;
    --orange: #f7ab3b;
    --purple: #70569f;
    --red: #ef5b47;
    --teal: #46bfa8;
  }
  * { box-sizing: border-box; margin: 0; padding: 0; }
  html, body { width: 1200px; height: 849px; overflow: hidden; background: var(--paper); }
  .sheet {
    position: relative; width: 1200px; height: 849px;
    background: var(--paper); border: 2px solid var(--frame);
    font-family: "Open Sans", Arial, sans-serif; color: var(--text);
  }
  .sheet-title {
    position: absolute; top: 42px; left: 0; width: 100%;
    text-align: center; font-family: "Bebas Neue", "Oswald", sans-serif;
    font-size: 66px; letter-spacing: 2px; color: var(--ink); line-height: 1;
  }
  .timeline { position: absolute; top: 122px; left: 168px; width: 860px; height: 28px; }
  .option {
    position: absolute; top: 186px; width: 194px;
  }
  .option-label {
    font-family: "Oswald", sans-serif; font-weight: 500; font-size: 27px;
    text-align: center; letter-spacing: 0.5px; height: 49px; line-height: 30px;
  }
  .option-head {
    height: 90px; color: #fff; display: flex; align-items: center; justify-content: center;
    text-align: center; font-weight: 600; font-size: 21px; line-height: 1.2; padding: 0 10px;
    box-shadow: 2px 3px 6px rgba(0,0,0,0.22);
  }
  .card {
    background: var(--paper); padding: 10px 9px 0;
    box-shadow: 2px 3px 7px rgba(0,0,0,0.22);
  }
  .card-title { font-size: 19px; font-weight: 400; padding-bottom: 6px; border-bottom: 1px solid var(--rule); }
  .card ul { list-style: none; }
  .card li {
    font-size: 11.5px; line-height: 1.35; padding: 6px 0 6px 2px;
    border-bottom: 1px solid var(--rule);
  }
  .pros { height: 138px; }
  .cons { position: absolute; left: 0; width: 194px; height: 300px; top: 301px; }
  .cons::after {
    content: ""; position: absolute; left: 0; right: 0; bottom: 0; height: 31px;
    background: var(--accent);
  }
  .option--blue { left: 74px; --accent: var(--blue); }
  .option--orange { left: 289px; --accent: var(--orange); }
  .option--purple { left: 503px; --accent: var(--purple); }
  .option--red { left: 717px; --accent: var(--red); }
  .option--teal { left: 932px; --accent: var(--teal); }
  .option-label, .card-title { color: var(--accent); }
  .option-head { background: var(--accent); }
  .option--teal .pros { height: 273px; }
  .option--teal .cons { top: 429px; height: 172px; }
</style>
</head>
<body>
<main class="sheet">
  <h1 class="sheet-title">Five Options – Divorce</h1>

  <svg class="timeline" viewBox="0 0 860 28" aria-hidden="true">
    <line x1="10" y1="14" x2="850" y2="14" stroke="#4b4b4d" stroke-width="3"/>
    <polygon points="4,2 24,14 4,26" fill="#4b4b4d"/>
    <polygon points="856,2 836,14 856,26" fill="#4b4b4d"/>
  </svg>

  <section class="option option--blue">
    <div class="option-label">OPTION 1</div>
    <div class="option-head">Do Nothing</div>
    <div class="card pros">
      <h2 class="card-title">Advantages:</h2>
      <ul><li>Stay married</li><li>No life Changes</li></ul>
    </div>
    <div class="card cons">
      <h2 class="card-title">Disadvantages:</h2>
      <ul>
        <li>Remain unhappy, depressed, anxious.</li>
        <li>Money and assets may disappear.</li>
        <li>What is going to change?</li>
      </ul>
    </div>
  </section>

  <section class="option option--orange">
    <div class="option-label">OPTION 2</div>
    <div class="option-head">Go to<br>Counseling</div>
    <div class="card pros">
      <h2 class="card-title">Advantages:</h2>
      <ul><li>Reconcile marriage</li><li>Help make a better life</li></ul>
    </div>
    <div class="card cons">
      <h2 class="card-title">Disadvantages:</h2>
      <ul>
        <li>Past issues are highlighted and may drudge up old wounds.</li>
        <li>It may just clarify the reasons you need to separate and/or divorce.</li>
        <li>Both parties must be invested and willing to participate.</li>
      </ul>
    </div>
  </section>

  <section class="option option--purple">
    <div class="option-label">OPTION 3</div>
    <div class="option-head">Do it Yourself</div>
    <div class="card pros">
      <h2 class="card-title">Advantages:</h2>
      <ul><li>No attorney fees</li><li>You are your on attorney</li></ul>
    </div>
    <div class="card cons">
      <h2 class="card-title">Disadvantages:</h2>
      <ul>
        <li>People often find that what is “fair,” may in fact, not be truly fair.</li>
        <li>Often times, people do not know the risks.</li>
        <li>Complicated legal system within intrigue rules.</li>
        <li>Unsure how to complete the necessary paperwork and meet the deadlines.</li>
      </ul>
    </div>
  </section>

  <section class="option option--red">
    <div class="option-label">OPTION 4</div>
    <div class="option-head">Limited<br>Representation</div>
    <div class="card pros">
      <h2 class="card-title">Advantages:</h2>
      <ul><li>Balance between going alone</li><li>and our limited involvement in the case</li></ul>
    </div>
    <div class="card cons">
      <h2 class="card-title">Disadvantages:</h2>
      <ul>
        <li>Our terms may not benefit from our legal knowledge.</li>
        <li>The legal consequences of your legal documents will not be explained to you so that you can formulate a plan for handling the rest of your case.</li>
        <li>Your spouse or other parties may cause your legal fees to increase significantly without action on your part.</li>
      </ul>
    </div>
  </section>

  <section class="option option--teal">
    <div class="option-label">OPTION 5</div>
    <div class="option-head">Hire Us</div>
    <div class="card pros">
      <h2 class="card-title">Advantages:</h2>
      <ul>
        <li>Gain the full benefits of our experience</li>
        <li>Have a team of Family Law focus attorneys</li>
        <li>Often saves you or makes you money in the long run</li>
        <li>Save you time, energy and stress</li>
      </ul>
    </div>
    <div class="card cons">
      <h2 class="card-title">Disadvantages:</h2>
      <ul><li>Initial cost</li></ul>
    </div>
  </section>
</main>
</body>
</html>
```